Business Card Design Project

Lorabelle is a women fashion house focusing on youthful glamour.

We bring together unique designs, premium quality materials and top craftsmanship to deliver sophisticated yet playful glamour, fun and excitement to the confident woman.

We can sum up the brand identity in 3 words:
Glamour – Sophistication – Unique

Industry/Entity Type

Fashion

Requirements
Must have
• Nim Ferrasco
nim.ferrasco@lorabelle-example.com
Mobile: 081 536 2947
Instragram: lorabelle_label
Facebook: lorabelle

Creative Director
Lorabelle Co., LTD
TEL: 02 631 48 97
42 Maple Row, 2nd Floor , D Building , Thonrak , Chaloemrat 28.
East Sanphet , Rattana , Bangkok 10240 Thailand
www.lorabelle-example.com

```html
<!DOCTYPE html>
<html lang="en">
<head>
<meta charset="utf-8">
<title>Lorabelle Business Card</title>
<link rel="stylesheet" href="https://fonts.googleapis.com/css2?family=Playfair+Display:wght@400&family=Roboto+Condensed:wght@400&display=swap">
<style>
  :root {
    --canvas-bg: #f4f4f2;
    --card-light: #ffffff;
    --card-dark: #161616;
    --card-dark-edge: #0b0b0b;
    --ink: #2a2a2a;
    --ink-soft: #555555;
    --icon: #333333;
    --logo-light: #ffffff;
  }
  * { margin: 0; padding: 0; box-sizing: border-box; }
  html, body {
    width: 1200px;
    height: 1000px;
    overflow: hidden;
    background: var(--canvas-bg);
  }
  .canvas {
    position: relative;
    width: 1200px;
    height: 1000px;
  }
  .card {
    position: absolute;
    top: 373px;
    width: 443px;
    height: 255px;
    border-radius: 4px;
  }
  .card--front {
    left: 82px;
    background: var(--card-light);
    box-shadow: 0 2px 5px rgba(0,0,0,0.18);
  }
  .card--back {
    left: 680px;
    background: var(--card-dark);
    border: 2px solid var(--card-dark-edge);
    box-shadow: 0 2px 5px rgba(0,0,0,0.25);
  }
  .wordmark {
    font-family: "Playfair Display", serif;
    font-weight: 400;
    letter-spacing: 0.5px;
    line-height: 1;
  }
  .card--front .wordmark {
    position: absolute;
    left: 19px;
    top: 18px;
    font-size: 38px;
    color: var(--ink);
  }
  .card--back .wordmark {
    position: absolute;
    left: 0;
    right: 0;
    top: 96px;
    text-align: center;
    font-size: 44px;
    color: var(--logo-light);
  }
  .holder {
    position: absolute;
    left: 242px;
    top: 14px;
    font-family: "Roboto Condensed", sans-serif;
    color: var(--ink);
  }
  .holder__name { font-size: 15px; line-height: 18px; }
  .holder__role { font-size: 12px; line-height: 15px; color: var(--ink-soft); }
  .contacts {
    position: absolute;
    left: 242px;
    top: 56px;
    list-style: none;
    font-family: "Roboto Condensed", sans-serif;
    font-size: 11.5px;
    color: var(--ink);
  }
  .contacts li {
    display: flex;
    align-items: center;
    height: 18px;
  }
  .contacts svg {
    width: 10px;
    height: 10px;
    margin-right: 12px;
    flex: none;
    fill: var(--icon);
  }
  .address {
    position: absolute;
    left: 242px;
    top: 175px;
    display: flex;
    font-family: "Roboto Condensed", sans-serif;
    font-size: 11.5px;
    line-height: 18px;
    color: var(--ink);
  }
  .address svg {
    width: 10px;
    height: 12px;
    margin: 3px 11px 0 0;
    flex: none;
    fill: var(--icon);
  }
</style>
</head>
<body>
<main class="canvas">

  <section class="card card--front" aria-label="Business card front">
    <div class="wordmark">Lorabelle</div>

    <div class="holder">
      <p class="holder__name">Nim Ferrasco</p>
      <p class="holder__role">Creative Director</p>
    </div>

    <ul class="contacts">
      <li>
        <svg viewBox="0 0 10 10" aria-hidden="true"><path d="M0 2h10v6H0z M0.8 2.6 5 5.6 9.2 2.6" fill="none" stroke="#333" stroke-width="1"/><rect x="0" y="2" width="10" height="6" fill="#333"/><path d="M0.5 2.5 5 5.5 9.5 2.5" fill="none" stroke="#fff" stroke-width="0.9"/></svg>
        nim.ferrasco@lorabelle-example.com
      </li>
      <li>
        <svg viewBox="0 0 10 10" aria-hidden="true"><rect x="2.5" y="0" width="5" height="10" rx="1"/><rect x="3.3" y="1.2" width="3.4" height="6.4" fill="#fff"/><circle cx="5" cy="8.7" r="0.5" fill="#fff"/></svg>
        081 536 2947
      </li>
      <li>
        <svg viewBox="0 0 10 10" aria-hidden="true"><path d="M2.2 0.5 3.9 2.6 2.9 3.9C3.5 5.3 4.7 6.5 6.1 7.1L7.4 6.1 9.5 7.8 8.6 9.4C4.6 9.5 0.5 5.4 0.6 1.4Z"/></svg>
        02 631 48 97
      </li>
      <li>
        <svg viewBox="0 0 10 10" aria-hidden="true"><rect x="0.5" y="0.5" width="9" height="9" rx="1.5"/></svg>
        lorabelle_label
      </li>
      <li>
        <svg viewBox="0 0 10 10" aria-hidden="true"><circle cx="5" cy="5" r="4.4" fill="none" stroke="#333" stroke-width="1"/><ellipse cx="5" cy="5" rx="1.9" ry="4.4" fill="none" stroke="#333" stroke-width="0.9"/><path d="M0.6 5h8.8M1.4 2.8h7.2M1.4 7.2h7.2" stroke="#333" stroke-width="0.8"/></svg>
        www.lorabelle-example.com
      </li>
      <li>
        <svg viewBox="0 0 10 10" aria-hidden="true"><rect x="0.5" y="0.5" width="9" height="9" rx="1"/></svg>
        lorabelle
      </li>
    </ul>

    <div class="address">
      <svg viewBox="0 0 10 12" aria-hidden="true"><path d="M5 0C2.4 0 0.8 1.9 0.8 4.1 0.8 7 5 12 5 12S9.2 7 9.2 4.1C9.2 1.9 7.6 0 5 0Z"/><circle cx="5" cy="4.2" r="1.6" fill="#fff"/></svg>
      <p>42 Maple Row, 2nd Floor , D Building ,<br>Thonrak , Chaloemrat 28.<br>East Sanphet , Rattana , Bangkok<br>10240 Thailand</p>
    </div>
  </section>

  <section class="card card--back" aria-label="Business card back">
    <div class="wordmark">Lorabelle</div>
  </section>

</main>
</body>
</html>
```